Consulting company business cards

We have a base design, but would be willing to update. We have a new logo/"tag" that needs to be added. Current business card design is attached for reference into our "style."

Industry/Entity Type

Business

Contact Information for Business Card

Should contain name and title, office number, mobile number if appropriate, e-mail, website, physical address, and company logo.

Font styles to use
Other font styles liked:
• See current card design on KorvandBCard

Colors
0455a3
85acd3
aaaaaa

Requirements
Must have
• Our colors are navy blue, gray, and a lighter blue
Nice to have
• Design that I can easily drop in new names/titles as we hire employees.

```html
<!DOCTYPE html>
<html lang="en">
<head>
<meta charset="utf-8">
<title>Tessaro Business Card</title>
<link href="https://fonts.googleapis.com/css2?family=Lato:wght@400;700&display=swap" rel="stylesheet">
<style>
  :root {
    --navy: #00324f;
    --sky: #7bafd4;
    --ink: #3f3f3f;
    --rule: #9a9a9a;
    --paper: #ffffff;
    --backdrop: #e4e4e4;
  }
  * { margin: 0; padding: 0; box-sizing: border-box; }
  html, body { width: 1200px; height: 750px; overflow: hidden; }
  body {
    background: var(--backdrop);
    font-family: "Lato", sans-serif;
    position: relative;
  }
  .card {
    position: absolute;
    top: 228px;
    width: 461px;
    height: 263px;
    border-radius: 13px;
    overflow: hidden;
  }
  .card-front { left: 124px; background: var(--paper); }
  .card-back { left: 618px; background: var(--navy); }

  .brand {
    position: absolute;
    left: 234px;
    top: 30px;
    width: 196px;
    text-align: center;
  }
  .brand-name {
    font-weight: 700;
    font-size: 44px;
    line-height: 50px;
    letter-spacing: 3px;
    color: var(--navy);
  }
  .brand-tag {
    font-size: 9.5px;
    letter-spacing: 1.8px;
    color: #6b6b6b;
    margin-top: 4px;
    white-space: nowrap;
  }

  .person-name {
    position: absolute; left: 29px; top: 118px;
    font-size: 20px; color: var(--navy);
  }
  .person-title {
    position: absolute; left: 29px; top: 142px;
    font-size: 15px; color: var(--sky);
  }
  .title-rule {
    position: absolute; left: 120px; top: 153px;
    width: 310px; height: 1px;
    background: linear-gradient(to right, var(--rule), rgba(154,154,154,0));
  }

  .contacts { position: absolute; left: 24px; top: 170px; list-style: none; }
  .contacts li {
    display: flex; align-items: center; gap: 5px;
    height: 17.5px; font-size: 13px; color: var(--ink);
  }
  .contacts svg { width: 13px; height: 12px; fill: var(--navy); }

  .address {
    position: absolute; right: 27px; top: 187px;
    text-align: right; font-size: 13px; line-height: 17.5px; color: var(--ink);
  }

  .footer-band { position: absolute; left: 0; bottom: 0; width: 461px; height: 29px; }
  .footer-web {
    position: absolute; right: 29px; bottom: 7px;
    font-size: 12.5px; letter-spacing: 1.2px; color: var(--paper);
  }

  .back-brand {
    position: absolute; left: 300px; top: 178px; width: 130px;
    text-align: center; font-weight: 700; font-size: 22px; letter-spacing: 2px;
    color: var(--paper);
  }
  .back-web {
    position: absolute; left: 290px; top: 219px; width: 150px;
    text-align: center; font-size: 13px; letter-spacing: 0.6px; color: var(--paper);
  }
</style>
</head>
<body>
  <section class="card card-front">
    <div class="brand">
      <div class="brand-name">TESSARO</div>
      <div class="brand-tag">A CLOUD CONSULTING COMPANY</div>
    </div>

    <div class="person-name">Renatakorvand</div>
    <div class="person-title">Office Manager</div>
    <div class="title-rule"></div>

    <ul class="contacts">
      <li>
        <svg viewBox="0 0 24 24" aria-hidden="true"><path d="M6.6 10.8a15.1 15.1 0 0 0 6.6 6.6l2.2-2.2a1 1 0 0 1 1-.25 11.4 11.4 0 0 0 3.6.57 1 1 0 0 1 1 1V20a1 1 0 0 1-1 1A17 17 0 0 1 3 4a1 1 0 0 1 1-1h3.5a1 1 0 0 1 1 1c0 1.25.2 2.45.57 3.57a1 1 0 0 1-.25 1z"/></svg>
        415.382.6604
      </li>
      <li>
        <svg viewBox="0 0 24 24" aria-hidden="true"><path d="M6 2h9l3 3v5H6z"/><path d="M2 11h20v7H2z"/><rect x="5" y="19" width="14" height="3"/></svg>
        415.382.6671
      </li>
      <li>
        <svg viewBox="0 0 24 24" aria-hidden="true"><path d="M2 5h20v14H2z M4 7l8 6 8-6" stroke="#fff" stroke-width="1.5"/></svg>
        rkorvand@tessarotech.com
      </li>
    </ul>

    <div class="address">1837 N Larkspur Ave<br>Fairmont Ohio 45219</div>

    <svg class="footer-band" viewBox="0 0 461 29" preserveAspectRatio="none" aria-hidden="true">
      <rect x="0" y="12" width="461" height="17" fill="var(--sky)"/>
      <path d="M244 29 C262 10 280 0 310 0 H461 V29 Z" fill="var(--navy)"/>
      <path d="M240 29 L244 29 C262 10 280 0 310 0 L306 0 C276 0 258 10 240 29 Z" fill="#ffffff"/>
    </svg>
    <div class="footer-web">www.tessarotech.com</div>
  </section>

  <section class="card card-back">
    <div class="back-brand">TESSARO</div>
    <div class="back-web">www.tessarotech.com</div>
  </section>
</body>
</html>
```